Novexa company website, a website for employment for people with autism

The website will make a match between people and jobs, mainly in the graphical sector, but also other sectors.
The name of the company is novexa and automates jobs with people that are on the autism spectrum.
The whole matchmaking and feedback process and so doesn't have to be in this prototype, we just want the general information pages and to convey a great look and brand identity that we will keep in the other pages to be developed. The website must be made with Wordpress, since the backend will be developed in Wordpress too.
It is a social project that wants to create possibilites for people with ASS to work from home for an employer or to do a variety of tasks for different customers.
The people we hire are generally not on the regular job market or have difficulty finding a job and "selling themselves"

Target Market(s)

matchmaking between talent (with ASS) and employers / jobs

Number of Pages Required

5+ page

Font styles to use
Sans Serif

Colors
ec1f27
e34298
a64599
6b449b
0355a3
0792cd

Requirements
Must have
• A stunning landing pages
• Integrate our logo and must match with what will do. We want a clean, modern, minimalistic, sleek website that radiates creativity and good looks.
• We have one page describing what we can do for customers, one page for people with ASS that would like to be candidates (our approach, learning program, ...), two pages that are addressed to partners who want to cooperate: the one's that can assist with autism related assistance and the one's that can help with the job coaching.
Nice to have
• In our logo are many colors as we embrace diversity and want to show that. Out main branding colors are red (for action) and blue for stability and will all gradients that go with it. Mainly white or black (or anthracite) for other parts
Should not have
• We want a modern and minimalistic design, no fluffy designs with lots of ornaments.

```html
<!DOCTYPE html>
<html lang="en">
<head>
<meta charset="utf-8">
<title>Novexa – Jobs for people on the autism spectrum</title>
<link rel="stylesheet" href="https://fonts.googleapis.com/css2?family=Montserrat:wght@500;600;700;800&family=Open+Sans:wght@400;600&display=swap">
<style>
:root{
  --red:#ec1f27;
  --pink:#e34298;
  --violet:#a64599;
  --purple:#6b449b;
  --blue:#0355a3;
  --sky:#0792cd;
  --ink:#1b1b1b;
  --text:#2a2a2a;
  --muted:#7a7a7a;
  --paper:#f3f3f3;
  --white:#ffffff;
}
*{margin:0;padding:0;box-sizing:border-box}
html,body{width:1200px;height:3209px;overflow:hidden}
body{position:relative;background:var(--white);font-family:"Open Sans",Arial,sans-serif;color:var(--text)}
.abs{position:absolute}
.heading{font-family:"Montserrat",Arial,sans-serif;font-weight:700;font-size:34px;line-height:42px;letter-spacing:0.3px;text-transform:uppercase;white-space:nowrap}
.copy{font-size:16.5px;line-height:27px}
.copy p+p{margin-top:27px}
.btn{display:flex;align-items:center;justify-content:center;font-family:"Montserrat",Arial,sans-serif;font-weight:700;font-size:16px;letter-spacing:0.5px;border-radius:30px;text-transform:uppercase;text-decoration:none}

/* Hero */
.hero{left:0;top:0;width:1200px;height:730px;background:#000;overflow:hidden}
.hero-visual{left:0;top:0;width:1200px;height:730px;
  background:
    radial-gradient(ellipse 260px 220px at 600px 420px,rgba(70,90,230,0.75),transparent 70%),
    radial-gradient(ellipse 420px 320px at 560px 260px,rgba(150,40,190,0.85),transparent 70%),
    radial-gradient(ellipse 300px 260px at 330px 300px,rgba(200,30,90,0.55),transparent 70%),
    radial-gradient(ellipse 300px 260px at 880px 250px,rgba(200,40,120,0.5),transparent 70%),
    radial-gradient(ellipse 560px 420px at 600px 340px,rgba(60,20,90,0.9),transparent 75%),
    #050208}
.brand{left:158px;top:30px;display:flex;align-items:center;gap:14px;font-family:"Montserrat",Arial,sans-serif;font-weight:600;font-size:34px;letter-spacing:3px;color:var(--white);text-transform:uppercase}
.brand-dot{width:26px;height:26px;border-radius:50%;background:var(--white)}
.main-nav{top:39px;height:22px;left:0;width:1200px}
.main-nav a{position:absolute;font-family:"Montserrat",Arial,sans-serif;font-weight:700;font-size:16px;color:var(--white);text-decoration:none;text-transform:uppercase;white-space:nowrap;transform:translateX(-50%)}
.hero-title{left:0;top:314px;width:1200px;text-align:center;font-family:"Montserrat",Arial,sans-serif;font-weight:800;color:var(--white);text-transform:uppercase}
.hero-title .line-1{display:block;font-size:47px;line-height:58px}
.hero-title .line-2{display:block;font-size:31px;line-height:39px;font-weight:700}

/* About */
.about{left:0;top:730px;width:1200px;height:620px;background:var(--white)}
.about .heading{left:171px;top:112px;color:var(--purple)}
.about .heading span{color:var(--pink)}
.about .copy{left:156px;top:186px;width:480px;color:var(--text)}
.about .btn{left:154px;top:376px;width:188px;height:58px;border:2px solid var(--red);color:var(--red);background:var(--white)}

/* Services */
.services{left:0;top:1350px;width:1200px;height:561px;background:var(--ink)}
.services .heading{left:638px;top:120px;color:var(--white);font-size:32px}
.services .copy{left:616px;top:196px;width:480px;color:var(--white)}
.services .btn{left:614px;top:383px;width:182px;height:56px;background:var(--white);color:var(--ink)}

/* Blogs */
.blogs{left:0;top:1911px;width:1200px;height:605px;background:var(--paper)}
.blogs .heading{left:0;top:63px;width:1200px;text-align:center;color:var(--blue)}
.blogs .heading span{color:var(--sky)}
.blog-card{top:160px;width:281px;height:346px;background:var(--white);box-shadow:0 2px 8px rgba(0,0,0,0.12)}
.blog-photo{left:0;top:0;width:281px;height:164px}
.blog-date{left:12px;top:148px;padding:4px 14px;background:var(--white);font-family:"Montserrat",Arial,sans-serif;font-weight:700;font-size:13px;color:var(--pink)}
.blog-title{left:26px;top:192px;width:245px;font-family:"Montserrat",Arial,sans-serif;font-weight:600;font-size:13px;line-height:20px;color:var(--sky);white-space:nowrap}
.blog-excerpt{left:26px;top:246px;width:240px;font-size:12px;line-height:17px;color:var(--muted)}
.blog-more{left:26px;top:306px;font-family:"Montserrat",Arial,sans-serif;font-weight:700;font-size:13px;color:var(--blue);text-decoration:none;text-transform:uppercase}

/* Contact */
.contact{left:0;top:2516px;width:1200px;height:543px;background:linear-gradient(115deg,var(--purple) 0%,#4b4aa6 40%,#1f6fbe 75%,#1584cc 100%)}
.contact .heading{left:180px;top:88px;color:var(--white);font-size:31px}
.contact-item{left:163px;color:var(--white)}
.contact-item svg{position:absolute;left:0;top:4px}
.contact-item h3{position:absolute;left:62px;top:0;white-space:nowrap;font-family:"Montserrat",Arial,sans-serif;font-weight:700;font-size:17px;text-transform:uppercase}
.contact-item p{position:absolute;left:62px;top:28px;white-space:nowrap;font-size:16.5px;line-height:28px}
.contact-form .field{position:absolute;left:522px;width:533px;background:var(--white);border-bottom:4px solid #3b3f9c;font-size:15px;color:#555;padding:12px 22px}
.contact-form .submit{position:absolute;left:526px;top:410px;width:171px;height:56px;background:var(--pink);color:var(--white);border:none;font-family:"Montserrat",Arial,sans-serif;font-weight:700;font-size:20px;text-transform:uppercase}

/* Footer */
.site-footer{left:0;top:3059px;width:1200px;height:150px;background:var(--white)}
.footer-brand{left:150px;top:42px;font-family:"Montserrat",Arial,sans-serif;font-weight:700;font-size:22px;letter-spacing:1px;color:var(--purple);text-transform:uppercase}
.footer-nav a{position:absolute;top:46px;font-family:"Montserrat",Arial,sans-serif;font-weight:600;font-size:15px;color:#555;text-decoration:none;text-transform:uppercase}
.copyright{left:347px;top:86px;font-size:13px;color:#888}
.social{top:41px;width:30px;height:30px;border-radius:50%;background:#2f5aa8}
</style>
</head>
<body>

<header class="abs hero">
  <div class="abs hero-visual" role="img" aria-label="Glowing purple, magenta and blue energy cloud on black background"></div>
  <svg class="abs" style="left:0;top:0" width="1200" height="730" viewBox="0 0 1200 730" aria-hidden="true">
    <defs>
      <linearGradient id="heroHex" x1="0" y1="0" x2="0" y2="1">
        <stop offset="0" stop-color="#a64599"/>
        <stop offset="1" stop-color="#ec1f27"/>
      </linearGradient>
    </defs>
    <polygon points="592,128 791,243 791,473 592,588 393,473 393,243" fill="none" stroke="url(#heroHex)" stroke-width="10"/>
    <line x1="592" y1="305" x2="592" y2="660" stroke="#fff" stroke-width="2"/>
    <circle cx="592" cy="272" r="33" fill="#fff"/>
    <circle cx="592" cy="272" r="28" fill="#000"/>
    <polygon points="584,257 584,287 607,272" fill="#fff"/>
    <polyline points="584,668 592,675 600,668" fill="none" stroke="#fff" stroke-width="2"/>
    <polyline points="584,678 592,685 600,678" fill="none" stroke="#fff" stroke-width="2"/>
  </svg>
  <div class="abs brand"><span class="brand-dot"></span>Novexa</div>
  <nav class="abs main-nav">
    <a href="#about" style="left:618px">About us</a>
    <a href="#services" style="left:734px">Services</a>
    <a href="#jobs" style="left:828px">Jobs</a>
    <a href="#blog" style="left:908px">Blog</a>
    <a href="#contact" style="left:1004px">Contact</a>
  </nav>
  <h1 class="abs hero-title">
    <span class="line-1">Automates jobs with</span>
    <span class="line-2">People that are on the</span>
    <span class="line-2">autism spectrum</span>
  </h1>
</header>

<section class="abs about" id="about">
  <svg class="abs" style="left:0;top:0" width="1200" height="620" viewBox="0 0 1200 620" aria-hidden="true">
    <defs>
      <linearGradient id="aboutTitleHex" x1="0" y1="0" x2="1" y2="1">
        <stop offset="0" stop-color="#a64599"/><stop offset="1" stop-color="#ec1f27"/>
      </linearGradient>
      <linearGradient id="leftHex" x1="0" y1="0" x2="0" y2="1">
        <stop offset="0" stop-color="#ec1f27"/><stop offset="1" stop-color="#6b449b"/>
      </linearGradient>
      <linearGradient id="rightHex" x1="0" y1="0" x2="1" y2="1">
        <stop offset="0" stop-color="#4fb6b0"/><stop offset="0.6" stop-color="#c6c43a"/><stop offset="1" stop-color="#c6c43a"/>
      </linearGradient>
      <linearGradient id="photoHex" x1="0" y1="0" x2="1" y2="1">
        <stop offset="0" stop-color="#a64599"/><stop offset="0.6" stop-color="#6b449b"/><stop offset="1" stop-color="#0792cd"/>
      </linearGradient>
      <linearGradient id="aboutPhoto" x1="0" y1="0" x2="1" y2="1">
        <stop offset="0" stop-color="#d9d4cc"/><stop offset="0.5" stop-color="#8d7768"/><stop offset="1" stop-color="#3e3a3c"/>
      </linearGradient>
    </defs>
    <polygon points="178,101 206,117 206,149 178,165 150,149 150,117" fill="none" stroke="url(#aboutTitleHex)" stroke-width="3"/>
    <polygon points="774,212 913,292 913,452 774,532 635,452 635,292" fill="none" stroke="url(#leftHex)" stroke-width="12"/>
    <polygon points="1003,241 1157,330 1157,508 1003,597 849,508 849,330" fill="none" stroke="url(#rightHex)" stroke-width="12"/>
    <polygon points="916,25 1105,134 1105,346 916,455 727,346 727,134" fill="url(#aboutPhoto)" stroke="url(#photoHex)" stroke-width="14" role="img" aria-label="Young man working on a laptop in an office"/>
  </svg>
  <h2 class="abs heading">About <span>Novexa</span></h2>
  <div class="abs copy">
    <p>Pellentesque faucibus Ut accumsan ultricies elit Maecenas at justo id velit placerat molestie Donec dictum lectus non odio Cras a ante vitae enim iaculis aliquam</p>
    <p>Mauris nunc quam venenatis nec euismod sit amet egestas placerat est Pellentesque habitant morbi tristique</p>
  </div>
  <a class="abs btn" href="#about">Learn more</a>
</section>

<section class="abs services" id="services">
  <svg class="abs" style="left:0;top:0" width="1200" height="561" viewBox="0 0 1200 561" aria-hidden="true">
    <defs>
      <linearGradient id="servHex" x1="0" y1="0" x2="0" y2="1">
        <stop offset="0" stop-color="#a64599"/><stop offset="1" stop-color="#ec1f27"/>
      </linearGradient>
      <linearGradient id="servPhoto" x1="0" y1="0" x2="1" y2="1">
        <stop offset="0" stop-color="#b89c86"/><stop offset="0.5" stop-color="#4d86c4"/><stop offset="1" stop-color="#2a2a33"/>
      </linearGradient>
    </defs>
    <polygon points="340,55 535,168 535,393 340,505 145,393 145,168" fill="url(#servPhoto)" stroke="url(#servHex)" stroke-width="14" role="img" aria-label="Man with a headset working at a computer desk"/>
    <polygon points="645,104 673,120 673,152 645,168 617,152 617,120" fill="none" stroke="#fff" stroke-width="3"/>
  </svg>
  <h2 class="abs heading">Our services</h2>
  <div class="abs copy">
    <p>Pellentesque faucibus Ut accumsan ultricies elit Maecenas at justo id velit placerat molestie Donec dictum lectus non odio Cras a ante vitae enim iaculis aliquam</p>
    <p>Mauris nunc quam venenatis nec euismod sit amet egestas placerat est Pellentesque habitant morbi tristique</p>
  </div>
  <a class="abs btn" href="#services">Learn more</a>
</section>

<section class="abs blogs" id="blog">
  <svg class="abs" style="left:436px;top:48px" width="64" height="72" viewBox="0 0 64 72" aria-hidden="true">
    <defs>
      <linearGradient id="blogHex" x1="0" y1="0" x2="1" y2="1">
        <stop offset="0" stop-color="#0355a3"/><stop offset="1" stop-color="#0792cd"/>
      </linearGradient>
    </defs>
    <polygon points="32,3 61,20 61,52 32,69 3,52 3,20" fill="none" stroke="url(#blogHex)" stroke-width="3"/>
  </svg>
  <h2 class="abs heading">Recent <span>blogs</span></h2>

  <article class="abs blog-card" style="left:158px">
    <div class="abs blog-photo" role="img" aria-label="Hands typing on a laptop keyboard" style="background:linear-gradient(135deg,#dfe2e6,#9ea3aa 60%,#5d6066)"></div>
    <span class="abs blog-date">JAN 29, 2019</span>
    <h3 class="abs blog-title">Lorem ipsum dolor sit amet con-<br>sectetuer adipiscing elit Nam</h3>
    <p class="abs blog-excerpt">Duis quam Nam eget lacus Aliquam erat volutpat Quisque dignissim congue leo Mauris vel lacus vitae felis</p>
    <a class="abs blog-more" href="#blog">Read more ›</a>
  </article>

  <article class="abs blog-card" style="left:471px">
    <div class="abs blog-photo" role="img" aria-label="Close view of hands on a laptop" style="background:linear-gradient(135deg,#b9c9d8,#6d8aa6 55%,#34475e)"></div>
    <span class="abs blog-date">JAN 25, 2019</span>
    <h3 class="abs blog-title">Lorem ipsum dolor sit amet con-<br>sectetuer adipiscing elit Nam</h3>
    <p class="abs blog-excerpt">Duis quam Nam eget lacus Aliquam erat volutpat Quisque dignissim congue leo Mauris vel lacus vitae felis</p>
    <a class="abs blog-more" href="#blog">Read more ›</a>
  </article>

  <article class="abs blog-card" style="left:783px">
    <div class="abs blog-photo" role="img" aria-label="Smiling young man in a suit at an office" style="background:linear-gradient(135deg,#7b8a45,#3f4a3a 50%,#1e2a46)"></div>
    <span class="abs blog-date">JAN 20, 2019</span>
    <h3 class="abs blog-title">Lorem ipsum dolor sit amet con-<br>sectetuer adipiscing elit Nam</h3>
    <p class="abs blog-excerpt">Duis quam Nam eget lacus Aliquam erat volutpat Quisque dignissim congue leo Mauris vel lacus vitae felis</p>
    <a class="abs blog-more" href="#blog">Read more ›</a>
  </article>
</section>

<section class="abs contact" id="contact">
  <svg class="abs" style="left:160px;top:74px" width="58" height="66" viewBox="0 0 58 66" aria-hidden="true">
    <polygon points="29,3 55,18 55,48 29,63 3,48 3,18" fill="none" stroke="#fff" stroke-width="3"/>
  </svg>
  <h2 class="abs heading">Contact us</h2>

  <div class="abs contact-item" style="top:177px">
    <svg width="26" height="32" viewBox="0 0 26 32" aria-hidden="true"><path d="M13 30C13 30 3 18 3 11a10 10 0 0 1 20 0c0 7-10 19-10 19z" fill="none" stroke="#fff" stroke-width="1.8"/><circle cx="13" cy="11" r="4" fill="none" stroke="#fff" stroke-width="1.8"/><path d="M4 30h18" stroke="#fff" stroke-width="1.5"/></svg>
    <h3>Address</h3>
    <p>48 Harbor Lane Suite 2B<br>Austin 78701 TX</p>
  </div>

  <div class="abs contact-item" style="top:288px">
    <svg width="32" height="32" viewBox="0 0 32 32" aria-hidden="true"><path d="M7 3l5 1 2 7-3 3c2 4 5 7 9 9l3-3 7 2 1 5-3 3C16 30 2 16 4 6z" fill="none" stroke="#fff" stroke-width="1.8" stroke-linejoin="round"/></svg>
    <h3>Phone number</h3>
    <p>555.014.2287</p>
  </div>

  <div class="abs contact-item" style="top:372px">
    <svg width="34" height="28" viewBox="0 0 34 28" aria-hidden="true"><rect x="2" y="3" width="30" height="22" fill="none" stroke="#fff" stroke-width="1.8"/><polyline points="2,3 17,16 32,3" fill="none" stroke="#fff" stroke-width="1.8"/><path d="M2 25l11-11M32 25L21 14" stroke="#fff" stroke-width="1.5"/></svg>
    <h3>Email address</h3>
    <p>hello@novexa-mail.com</p>
  </div>

  <form class="contact-form" action="#">
    <div class="field" style="top:106px;height:46px">Name</div>
    <div class="field" style="top:162px;height:47px">Email address</div>
    <div class="field" style="top:220px;height:47px">Phone</div>
    <div class="field" style="top:278px;height:111px">Message</div>
    <button class="submit" type="submit">Submit</button>
  </form>
</section>

<footer class="abs site-footer">
  <div class="abs footer-brand">Novexa</div>
  <nav class="footer-nav">
    <a href="#about" style="left:347px">About us</a>
    <a href="#services" style="left:464px">Services</a>
    <a href="#jobs" style="left:578px">Jobs</a>
    <a href="#blog" style="left:655px">Blog</a>
    <a href="#contact" style="left:734px">Contact</a>
  </nav>
  <p class="abs copyright">© 2019 Company Name &nbsp;All right reserved</p>
  <span class="abs social" style="left:879px" aria-label="Social link"></span>
  <span class="abs social" style="left:918px" aria-label="Social link"></span>
  <span class="abs social" style="left:956px" aria-label="Social link"></span>
  <span class="abs social" style="left:995px" aria-label="Social link"></span>
</footer>

</body>
</html>
```